Infographic

We are looking for a new concept on a particular PPT slide to communicate a before and after scenario.
Updates

Note that this is a B2B (telecom) technology exercise and are looking for two other ideas to decision makers at billion dollar companies in various verticals. 

Target Market(s)

CIOs, CTOs

```html
<!DOCTYPE html>
<html lang="en">
<head>
<meta charset="utf-8">
<title>Super Node Carrier Competition</title>
<link href="https://fonts.googleapis.com/css2?family=Arimo:wght@400;700&display=swap" rel="stylesheet">
<style>
  :root {
    --header-blue: #4c86b8;
    --heading-blue: #4a8cc4;
    --arrow-blue: #4f90c6;
    --ring-blue: #a9c8e4;
    --bg-top: #ffffff;
    --bg-bottom: #e6e7e9;
    --circle-gray: #c9cacc;
    --text-dark: #1e1e1e;
    --white: #ffffff;
    --node-dark: #7d858c;
    --node-light: #d9dde1;
  }
  * { margin: 0; padding: 0; box-sizing: border-box; }
  html, body { width: 1200px; height: 849px; overflow: hidden; }
  body {
    font-family: "Arimo", Arial, sans-serif;
    background: #ffffff;
    color: var(--text-dark);
  }
  .slide {
    position: relative;
    width: 1200px;
    height: 849px;
    background: radial-gradient(ellipse at 50% 45%, var(--bg-top) 0%, #f3f3f4 50%, var(--bg-bottom) 100%);
    overflow: hidden;
  }
  .header-band {
    position: absolute; left: 0; top: 0; width: 1200px; height: 117px;
    background: var(--header-blue);
    display: flex; align-items: center; justify-content: center;
  }
  .header-band h1 {
    color: var(--white); font-size: 36px; font-weight: 700;
    line-height: 44px; text-align: center;
  }
  .section-heading {
    position: absolute; top: 146px; font-size: 27px; font-weight: 700;
    color: var(--heading-blue);
  }
  .section-heading.old { left: 36px; }
  .section-heading.new { left: 588px; }

  .carrier-circle {
    position: absolute; left: 65px; top: 262px; width: 300px; height: 300px;
    border-radius: 50%; background: radial-gradient(circle at 50% 40%, #d8d9db, var(--circle-gray));
  }
  .phone-art {
    position: absolute; left: 75px; top: 40px; width: 150px; height: 150px;
    border-radius: 20px; background: radial-gradient(circle, #4a4a4a, #1c1c1c 70%);
  }
  .carrier-label {
    position: absolute; left: 0; top: 218px; width: 300px; text-align: center;
    font-size: 22px; line-height: 30px;
  }
  .old-caption {
    position: absolute; left: 58px; top: 604px; width: 420px;
    font-size: 16.5px; line-height: 22px;
  }

  .migrate-arrow { position: absolute; left: 387px; top: 358px; }
  .migrate-text {
    position: absolute; left: 394px; top: 384px; width: 180px; text-align: center;
    color: var(--white); font-size: 15.5px; font-weight: 700; line-height: 20px;
  }

  .network-map { position: absolute; left: 640px; top: 200px; }
  .super-node {
    position: absolute; width: 88px; height: 104px; border-radius: 6px;
    background: linear-gradient(90deg, var(--node-dark), var(--node-light) 50%, var(--node-dark));
  }
  .super-node span {
    position: absolute; left: 0; right: 0; bottom: 10px; text-align: center;
    color: var(--white); font-size: 13px;
  }
  .node-top { left: 856px; top: 200px; }
  .node-left { left: 667px; top: 405px; }
  .node-right { left: 1036px; top: 405px; }
  .node-bottom { left: 856px; top: 580px; }

  .customer-icon {
    position: absolute; left: 860px; top: 355px; width: 76px; height: 76px;
  }
  .customer-label {
    position: absolute; left: 780px; top: 451px; width: 240px; text-align: center;
    font-size: 21px;
  }
  .customer-dc {
    position: absolute; left: 885px; top: 492px; width: 30px; height: 68px; border-radius: 3px;
    background: linear-gradient(90deg, #9aa1a7, #eef0f2 50%, #9aa1a7);
  }
  .customer-dc-label {
    position: absolute; left: 924px; top: 506px; font-size: 13px; line-height: 16px;
  }
  .new-caption {
    position: absolute; left: 685px; top: 700px; width: 430px; text-align: center;
    font-size: 16.5px; line-height: 22px;
  }

  .brand {
    position: absolute; left: 40px; top: 722px; display: flex; align-items: center; gap: 10px;
  }
  .brand-mark { width: 40px; height: 40px; border-radius: 50%; background: var(--header-blue); }
  .brand-name { font-size: 28px; color: var(--header-blue); }

  .footnote {
    position: absolute; left: 292px; top: 812px; font-size: 15.5px; font-weight: 700;
  }
</style>
</head>
<body>
<main class="slide">
  <header class="header-band">
    <h1>The leading, proven approach uses intense carrier<br>competition among “super nodes.”</h1>
  </header>

  <h2 class="section-heading old">Old World: Carriers Dictate Prices</h2>
  <h2 class="section-heading new">New World: Competitive Market Lowers Prices</h2>

  <div class="carrier-circle">
    <div class="phone-art" role="img" aria-label="Illustration of a black rotary telephone"></div>
    <p class="carrier-label">Carrier at<br>the Center</p>
  </div>
  <p class="old-caption">Carrier sells or resells connections to corporate campuses, branches, processing centers, trading partners, application providers</p>

  <svg class="migrate-arrow" width="240" height="150" viewBox="0 0 240 150">
    <polygon points="0,10 192,10 192,0 236,72 192,144 192,134 0,134" fill="var(--arrow-blue)"/>
  </svg>
  <p class="migrate-text">Migrate safely from bloated MPLS, optical ring and Internet access services</p>

  <svg class="network-map" width="530" height="520" viewBox="640 200 530 520" style="left:640px;top:200px">
    <g fill="none" stroke="var(--ring-blue)">
      <circle cx="900" cy="457" r="210" stroke-width="2"/>
      <circle cx="900" cy="457" r="218" stroke-width="2"/>
      <circle cx="900" cy="457" r="226" stroke-width="2"/>
      <circle cx="900" cy="457" r="234" stroke-width="2"/>
    </g>
    <path d="M885 535 C 850 545, 840 600, 870 640" fill="none" stroke="var(--arrow-blue)" stroke-width="3"/>
  </svg>

  <div class="super-node node-top" role="img" aria-label="Server rack illustration"><span>super node</span></div>
  <div class="super-node node-left" role="img" aria-label="Server rack illustration"><span>super node</span></div>
  <div class="super-node node-right" role="img" aria-label="Server rack illustration"><span>super node</span></div>
  <div class="super-node node-bottom" role="img" aria-label="Server rack illustration"><span>super node</span></div>

  <svg class="customer-icon" viewBox="0 0 76 76" aria-label="Customer icon" role="img">
    <rect x="1.5" y="1.5" width="73" height="73" fill="var(--arrow-blue)" stroke="#2f6a9c" stroke-width="3"/>
    <circle cx="38" cy="28" r="12" fill="var(--white)"/>
    <path d="M16 66 C 16 48, 60 48, 60 66 Z" fill="var(--white)"/>
  </svg>
  <p class="customer-label">Customer at the Center</p>

  <div class="customer-dc" role="img" aria-label="Small server illustration"></div>
  <p class="customer-dc-label">Customer’s<br>Data Center</p>

  <p class="new-caption">Carrier sells only short tails to third-party data centers that are connected by hundreds of connectivity providers with high performance circuits</p>

  <div class="brand">
    <span class="brand-mark"></span>
    <span class="brand-name">Norvale Networks</span>
  </div>

  <p class="footnote">Super nodes are transit points within third-party data centers run by leading companies like Meridex, Transia and Hubline.</p>
</main>
</body>
</html>
```